Quillmarsh Property Solutions need a business card design

Hello guys. We would need a business card design asap please.
We are a start up property investment business based in London UK specialised in buying, selling, managing and letting properties and helping distressed property owners.
The name of our Business is Quillmarsh, the logo symbolises the four fundamental elements of the world (earth, air, fire and water) and so it stands for strength, stability, longevity.
We would like the business card to communicate professionalism and reliability. Many many thanks indeed for your work.

Details:

1.) Rosalind Updike
Property Investor
Mobile: +44(0)7700123456
Email: rosalind.quillmarsh@mailbox-example.com

2.) Dominic Updike
Property Investor
Mobile: +44(0)7700987654
Email: dominic.quillmarsh@mailbox-example.com

```html
<!DOCTYPE html>
<html lang="en">
<head>
<meta charset="utf-8">
<title>Quillmarsh Property Solutions – Business Card</title>
<link rel="stylesheet" href="https://fonts.googleapis.com/css2?family=Jost:wght@400;500;600&family=Open+Sans:wght@400;700&display=swap">
<style>
  :root {
    --backdrop: #e9e7e4;
    --card: #ffffff;
    --band-blue: #1d5f86;
    --ink-dark: #4b4b4d;
    --ink-grey: #555558;
    --name-blue: #1f5f86;
    --accent-green: #1e6b35;
    --accent-red: #d3302b;
    --rule: #6d6d6d;
    --mark-faint: #c9d3db;
  }
  * { box-sizing: border-box; margin: 0; padding: 0; }
  html, body {
    width: 1200px; height: 900px; overflow: hidden;
    background: var(--backdrop);
  }
  .canvas { position: relative; width: 1200px; height: 900px; }

  .card {
    position: absolute;
    background: var(--card);
    box-shadow: 0 4px 14px rgba(0,0,0,0.12);
    overflow: hidden;
  }
  .card--front { left: 50px; top: 60px; width: 600px; height: 360px; }
  .card--back { left: 540px; top: 470px; width: 620px; height: 380px; }

  /* Front */
  .brand {
    position: absolute; left: 56px; top: 70px;
    display: flex; align-items: center; gap: 22px;
  }
  .brand__square { width: 62px; height: 62px; background: var(--ink-dark); }
  .brand__name {
    font-family: "Jost", sans-serif; font-weight: 600; color: var(--ink-dark);
    text-transform: uppercase; line-height: 1;
  }
  .brand__word { display: block; font-size: 52px; letter-spacing: 1px; }
  .brand__sub { display: block; font-size: 21px; letter-spacing: 1.5px; margin-top: 8px; padding-left: 40px; }

  .band {
    position: absolute; left: 0; bottom: 0; width: 100%; height: 140px;
    background: var(--band-blue);
    display: flex; align-items: center; justify-content: center;
  }
  .band__tagline {
    font-family: "Jost", sans-serif; font-weight: 500; font-size: 17px;
    color: #fff; text-transform: uppercase; text-align: center;
    letter-spacing: 0.6px; line-height: 1.35;
  }

  /* Back */
  .back-mark {
    position: absolute; top: 44px; left: 0; width: 100%;
    text-align: center;
    font-family: "Jost", sans-serif; font-weight: 600; font-size: 30px;
    letter-spacing: 2px; text-transform: uppercase; color: var(--mark-faint);
  }
  .contact {
    position: absolute; left: 0; width: 100%;
    display: flex; align-items: flex-start;
  }
  .contact--first { top: 196px; }
  .contact--second { top: 290px; }
  .contact__person { width: 240px; text-align: right; flex: none; }
  .contact__name {
    font-family: "Open Sans", sans-serif; font-weight: 700; font-size: 19px;
    color: var(--name-blue); line-height: 1.1;
  }
  .contact__role {
    font-family: "Jost", sans-serif; font-size: 15.5px; color: var(--ink-grey);
    margin-top: 2px;
  }
  .contact__lines {
    margin-left: 36px;
    font-family: "Jost", sans-serif; font-size: 15px; color: var(--ink-grey);
    line-height: 27px; margin-top: -4px;
    white-space: nowrap;
  }
  .contact__label { display: inline-block; width: 22px; font-weight: 600; }
  .contact--first .contact__label { color: var(--accent-green); }
  .contact--second .contact__label { color: var(--accent-red); }
  .divider {
    position: absolute; left: 66px; right: 66px; top: 268px;
    border-top: 1px solid var(--rule);
  }
</style>
</head>
<body>
<main class="canvas">
  <section class="card card--front" aria-label="Card front">
    <div class="brand">
      <span class="brand__square"></span>
      <h1 class="brand__name">
        <span class="brand__word">Quillmarsh</span>
        <span class="brand__sub">Property Solutions</span>
      </h1>
    </div>
    <div class="band">
      <p class="band__tagline">Buying, selling, managing, letting properties &amp;<br>helping distressed property owners.</p>
    </div>
  </section>

  <section class="card card--back" aria-label="Card back">
    <div class="back-mark">Quillmarsh</div>

    <div class="contact contact--first">
      <div class="contact__person">
        <p class="contact__name">Rosalind Updike</p>
        <p class="contact__role">Property Investor</p>
      </div>
      <div class="contact__lines">
        <p><span class="contact__label">M</span>+44(0)7700123456</p>
        <p><span class="contact__label">E</span>rosalind.quillmarsh@mailbox-example.com</p>
      </div>
    </div>

    <div class="divider"></div>

    <div class="contact contact--second">
      <div class="contact__person">
        <p class="contact__name">Dominic Updike</p>
        <p class="contact__role">Property Investor</p>
      </div>
      <div class="contact__lines">
        <p><span class="contact__label">M</span>+44(0)7700987654</p>
        <p><span class="contact__label">E</span>dominic.quillmarsh@mailbox-example.com</p>
      </div>
    </div>
  </section>
</main>
</body>
</html>
```